Healthcare/Medical Consultant Company

QRN is a Healthcare Conultant Company. We help doctors manage the business side of their medical practice.
We already have a very basic world press design. We want an upgraded design that conveys partnership, healthcare expertise and healthcare innovation to our client. It needs to have a sleek, clean, modern and inclusive look. Pictures need need to convey diversity (including pictures of people of all races and shows both men and women working together in a healthcare environment to make it better). The Pictures on the home page should particularly illustrate diversity and Healthcare expertise. The company logo is blue and white but the site doesn’t have to follow the exact same theme but the logo needs to blend well with the chosen theme. The logo should ideally be in the header of the website. We would also like the following included in our website:

1. Pages should include: a home page, About Us page, Services page, Get a quote page, Contact Us page, Staff page(where we can add pictures and bio for staff).

2. The Drop down menu for services should have hyperlinks ( for each service)Leading to a page that provides detailed info about that specific service. Our services include: Revenue Cycle Management, Regulatory Compliance, Human Resources Management, & practice Management.

3. Links to social media should in the header or footer of each page.

4. Contact info should be in the footer of each page.

5. Clients should be an email to us from the contact page.

Target Market(s)

Physician Medical Practices

Industry/Entity Type

Medical

Coding

Coded - Design and coding required

Font styles to use
Sans Serif

Colors

Designer to choose colors to be used in the design.

Requirements
Must have
• See project description
Nice to have
• See project description

```html
<!DOCTYPE html>
<html lang="en">
<head>
<meta charset="utf-8">
<title>QRN – Healthcare Consulting</title>
<link href="https://fonts.googleapis.com/css2?family=Montserrat:wght@400;600;700;800&family=Open+Sans:wght@400;600&display=swap" rel="stylesheet">
<style>
:root{
  --navy:#0b2a6b;
  --blue:#1450b4;
  --bright:#1e6fd9;
  --sky:#d6e6f8;
  --text:#4a5566;
  --muted:#8a94a3;
  --white:#ffffff;
  --paper:#f6f8fb;
}
*{box-sizing:border-box;margin:0;padding:0}
html,body{width:1200px;height:3040px;overflow:hidden;background:var(--white)}
body{position:relative;font-family:"Open Sans",Arial,sans-serif;color:var(--text)}
h2,h3,.brand,.nav a,.btn{font-family:"Montserrat",Arial,sans-serif}

/* header */
.site-header{position:absolute;top:0;left:0;width:1200px;height:64px;background:var(--white);z-index:5;box-shadow:0 2px 8px rgba(0,0,0,.06)}
.brand{position:absolute;left:120px;top:10px;display:flex;flex-direction:column;align-items:center;color:var(--navy)}
.brand .mark{font-size:30px;font-weight:800;letter-spacing:2px;line-height:1}
.brand .sub{font-size:8px;font-weight:800;letter-spacing:1px;margin-top:4px}
.nav{position:absolute;right:150px;top:24px;display:flex;gap:26px}
.nav a{font-size:12px;font-weight:600;color:var(--navy);text-decoration:none;letter-spacing:.5px}
.nav a.active{color:var(--bright);border-bottom:2px solid var(--bright);padding-bottom:4px}

/* hero */
.hero-photo{position:absolute;top:64px;left:0;width:1200px;height:600px;background:linear-gradient(120deg,#c9d3dc 0%,#eef1f3 35%,#b9c4cf 60%,#e3e7ea 100%)}
.hero-panel{position:absolute;left:720px;top:320px;width:300px;padding:20px 24px;background:rgba(255,255,255,.85)}
.hero-panel h1{font-family:"Montserrat",Arial,sans-serif;font-weight:800;font-size:34px;line-height:1.05;color:var(--navy);white-space:nowrap}
.hero-panel h1 span{color:var(--blue);display:block}
.btn{display:inline-block;font-size:11px;font-weight:700;letter-spacing:.5px;padding:8px 18px;text-decoration:none}
.btn.solid{background:var(--blue);color:var(--white)}
.btn.outline{border:1px solid var(--blue);color:var(--blue);background:var(--white)}
.hero-panel .btn{margin-top:14px}
.dots{position:absolute;top:568px;left:560px;display:flex;gap:8px}
.dots i{width:8px;height:8px;border-radius:50%;background:rgba(255,255,255,.7)}
.dots i:first-child{background:var(--white)}
.hero-wave{position:absolute;top:560px;left:0}

/* about */
.section-title{position:absolute;left:0;width:1200px;text-align:center;font-size:28px;font-weight:700;color:var(--navy);letter-spacing:.5px}
.about-text{position:absolute;top:770px;left:330px;width:540px;text-align:center;font-size:15px;line-height:1.6;color:var(--text)}
.about-btn{position:absolute;top:918px;left:548px}

/* services */
.services{position:absolute;top:1030px;left:0;width:1200px;height:560px;background:linear-gradient(180deg,#1a5dc4 0%,#0f3f9a 100%);overflow:hidden}
.services .section-title{top:60px;color:var(--white);font-size:22px}
.title-rule{position:absolute;top:96px;left:560px;width:80px;height:2px;background:var(--white)}
.svc-ring{position:absolute;left:0;top:0}
.hub{position:absolute;left:500px;top:165px;width:200px;height:200px;border-radius:50%;background:var(--white);display:flex;flex-direction:column;align-items:center;justify-content:center;color:var(--navy)}
.hub .mark{font-family:"Montserrat",Arial,sans-serif;font-size:54px;font-weight:800;letter-spacing:3px;line-height:1}
.hub .sub{font-family:"Montserrat",Arial,sans-serif;font-size:7.5px;font-weight:800;margin-top:6px;letter-spacing:.3px;white-space:nowrap}
.svc{position:absolute;width:220px;color:var(--white)}
.svc h3{font-size:15px;font-weight:700;line-height:1.25}
.svc p{font-size:10px;line-height:1.45;margin-top:6px;opacity:.85}
.svc .more{display:block;font-family:"Montserrat",Arial,sans-serif;font-size:9px;font-weight:700;margin-top:6px}
.svc.left{text-align:right}
.icon{position:absolute;width:56px;height:56px;border-radius:50%;border:2px solid var(--white);background:rgba(255,255,255,.08)}

/* mission */
.mission-photo{position:absolute;top:1590px;left:0;width:1200px;height:510px;background:linear-gradient(100deg,#5b6f84 0%,#9aa9b6 45%,#c7d0d8 70%,#7d8fa0 100%)}
.mission-card{position:absolute;top:1730px;left:160px;width:370px;padding:26px 30px;background:var(--white);box-shadow:0 6px 20px rgba(0,0,0,.15)}
.mission-card h2{font-size:22px;font-weight:700;color:var(--blue)}
.mission-card p{font-size:12px;line-height:1.6;margin-top:12px}
.mission-card .btn{margin-top:16px}

/* team */
.team{position:absolute;top:2240px;left:0;width:1200px}
.member{position:absolute;top:0;width:220px;text-align:center}
.member .portrait{width:150px;height:150px;margin:0 auto;border-radius:50%;border:6px solid var(--sky);background:linear-gradient(160deg,#c9d4de,#8a9bab)}
.member h3{font-size:16px;font-weight:700;color:var(--navy);margin-top:16px}
.member .role{font-size:11px;color:var(--muted);margin-top:4px}
.member p{font-size:10px;line-height:1.5;color:var(--muted);margin-top:10px}
.arrow{position:absolute;top:2300px}

/* footer */
.footer-wave{position:absolute;top:2590px;left:0}
.footer{position:absolute;top:2680px;left:0;width:1200px;height:300px;background:linear-gradient(180deg,#1553bb,#0d3a8f)}
.footer .brand-foot{position:absolute;left:140px;top:70px;color:var(--white);font-family:"Montserrat",Arial,sans-serif;font-size:56px;font-weight:800;letter-spacing:4px}
.fcol{position:absolute;top:60px;color:var(--white)}
.fcol h4{font-family:"Montserrat",Arial,sans-serif;font-size:13px;font-weight:700;letter-spacing:.5px;margin-bottom:12px}
.fcol li{list-style:none;font-size:12px;line-height:1.75}
.contact-line{display:flex;gap:8px;align-items:flex-start;font-size:12px;line-height:1.6;margin-bottom:6px}
.social{display:flex;gap:8px}
.social i{width:26px;height:26px;border-radius:50%;border:1.5px solid var(--white)}
.bottom-bar{position:absolute;top:2980px;left:0;width:1200px;height:60px;background:#0a2f78;color:rgba(255,255,255,.8);font-size:11px;text-align:center;line-height:60px}
</style>
</head>
<body>

<header class="site-header">
  <div class="brand"><span class="mark">QRN</span><span class="sub">QUALITY RESOURCE NETWORK LLC</span></div>
  <nav class="nav">
    <a class="active" href="#">HOME</a><a href="#">ABOUT US</a><a href="#">SERVICES</a><a href="#">GET A QUOTE</a><a href="#">CONTACT US</a><a href="#">STAFF</a>
  </nav>
</header>

<div class="hero-photo" role="img" aria-label="Diverse team of doctors and consultants meeting around a table in a bright office"></div>
<div class="hero-panel">
  <h1>ADVANCING<span>HEALTHCARE</span></h1>
  <a class="btn solid" href="#">Read More</a>
</div>
<div class="dots"><i></i><i></i><i></i><i></i></div>
<svg class="hero-wave" width="1200" height="110" viewBox="0 0 1200 110">
  <path d="M0 60 Q600 130 1200 40 L1200 110 L0 110 Z" fill="#1450b4" opacity=".9"/>
  <path d="M0 72 Q600 140 1200 56 L1200 110 L0 110 Z" fill="#ffffff"/>
</svg>

<h2 class="section-title" style="top:700px">ABOUT QRN</h2>
<p class="about-text">Quality Resource Network (QRN) is a healthcare consulting firm skilled at helping physician practices advance their strategic vision in an ever-evolving healthcare system. Quality Resource Network specializes in revenue cycle optimization, practice management improvement and developing new physician practices.</p>
<a class="btn outline about-btn" href="#">READ MORE</a>

<section class="services">
  <h2 class="section-title">OUR SERVICES</h2>
  <div class="title-rule"></div>
  <svg class="svc-ring" width="1200" height="560" viewBox="0 0 1200 560">
    <circle cx="600" cy="265" r="140" fill="none" stroke="#ffffff" stroke-opacity=".35" stroke-width="2"/>
    <circle cx="600" cy="265" r="122" fill="none" stroke="#ffffff" stroke-opacity=".2" stroke-width="1"/>
  </svg>
  <div class="hub"><span class="mark">QRN</span><span class="sub">QUALITY RESOURCE NETWORK LLC</span></div>

  <div class="icon" style="left:452px;top:150px"></div>
  <div class="icon" style="left:692px;top:150px"></div>
  <div class="icon" style="left:452px;top:326px"></div>
  <div class="icon" style="left:692px;top:326px"></div>

  <div class="svc left" style="left:210px;top:150px"><h3>Revenue Cycle Management</h3><p>In today's environment, steady cash flow requires careful attention at every step.</p><span class="more">READ MORE</span></div>
  <div class="svc" style="left:770px;top:150px"><h3>Practice Management</h3><p>Practice management is challenging, and we bring the right balance of skill and experience.</p><span class="more">READ MORE</span></div>
  <div class="svc left" style="left:210px;top:326px"><h3>Regulatory &amp; Compliance Management</h3><p>In a heavily regulated field, practices need to stay current on every new rule.</p><span class="more">READ MORE</span></div>
  <div class="svc" style="left:770px;top:326px"><h3>Human Resources Management</h3><p>Recruiting and retaining staff is key, and our team helps your people thrive.</p><span class="more">READ MORE</span></div>
</section>

<div class="mission-photo" role="img" aria-label="Diverse medical professionals reviewing documents together at a desk"></div>
<div class="mission-card">
  <h2>OUR MISSION</h2>
  <p>We partner with physician practices so they can focus on patient care. Our team brings trusted guidance, sound operations and lasting growth to every client we serve.</p>
  <a class="btn outline" href="#">READ MORE</a>
</div>

<h2 class="section-title" style="top:2160px;font-size:24px">EMPLOYEE PROFILE</h2>
<svg class="arrow" style="left:150px" width="24" height="40" viewBox="0 0 24 40"><path d="M18 4 L6 20 L18 36" fill="none" stroke="#8a94a3" stroke-width="3"/></svg>
<svg class="arrow" style="left:1026px" width="24" height="40" viewBox="0 0 24 40"><path d="M6 4 L18 20 L6 36" fill="none" stroke="#8a94a3" stroke-width="3"/></svg>
<div class="team">
  <div class="member" style="left:220px"><div class="portrait" role="img" aria-label="Staff member portrait"></div><h3>Member Name</h3><div class="role">Post Designation</div><p>Short bio about this staff member, their role and years of healthcare experience.</p></div>
  <div class="member" style="left:490px"><div class="portrait" role="img" aria-label="Staff member portrait"></div><h3>Member Name</h3><div class="role">Post Designation</div><p>Short bio about this staff member, their role and years of healthcare experience.</p></div>
  <div class="member" style="left:760px"><div class="portrait" role="img" aria-label="Staff member portrait"></div><h3>Member Name</h3><div class="role">Post Designation</div><p>Short bio about this staff member, their role and years of healthcare experience.</p></div>
</div>

<svg class="footer-wave" width="1200" height="92" viewBox="0 0 1200 92">
  <path d="M0 50 Q600 -10 1200 50 L1200 92 L0 92 Z" fill="#1553bb"/>
  <path d="M0 40 Q600 -20 1200 40" fill="none" stroke="#1e6fd9" stroke-width="2" opacity=".5"/>
</svg>
<footer class="footer">
  <div class="brand-foot">QRN</div>
  <div class="fcol" style="left:420px">
    <h4>QUICK LINKS</h4>
    <ul><li>Home</li><li>About Us</li><li>Services</li><li>Get a Quote</li><li>Contact Us</li></ul>
  </div>
  <div class="fcol" style="left:620px">
    <h4>CONTACT US</h4>
    <div class="contact-line"><svg width="12" height="16" viewBox="0 0 12 16"><path d="M6 1a5 5 0 0 1 5 5c0 4-5 9-5 9S1 10 1 6a5 5 0 0 1 5-5z" fill="#fff"/></svg><span>128 Harbor Lane Suite 410<br>Riverton, NY 10000</span></div>
    <div class="contact-line"><svg width="12" height="14" viewBox="0 0 12 14"><path d="M2 1h3l1 3-2 1a7 7 0 0 0 3 4l1-2 3 1v3a1 1 0 0 1-1 1A10 10 0 0 1 1 2a1 1 0 0 1 1-1z" fill="#fff"/></svg><span>(555) 010-4420</span></div>
    <div class="contact-line"><svg width="14" height="12" viewBox="0 0 14 12"><rect x="1" y="1" width="12" height="10" fill="none" stroke="#fff" stroke-width="1.5"/><path d="M1 1l6 5 6-5" fill="none" stroke="#fff" stroke-width="1.5"/></svg><span>info@qrnhealth.example</span></div>
  </div>
  <div class="fcol" style="left:900px">
    <h4>FOLLOW US</h4>
    <div class="social"><i></i><i></i><i></i><i></i></div>
  </div>
</footer>
<div class="bottom-bar">© 2018 Quality Resource Network. All rights reserved. Terms of Use</div>

</body>
</html>
```